Vietnam Recruitment Tour Postcard

We need a postcard to market a U.S. university student recruitment tour in northern Vietnam. The fair tour is organized by StudyBridgeNet which is a program of the Federal Bureau of Outreach www.studybridgenet.outreach-example.org

The audience for these postcards are U.S. higher education recruiters (not students). We want U.S. universities to sign up for the fair tour.

The postcards will be handed out at large education conferences.

Target Market(s)

U.S. university recruiters who are between the ages of 25 and 45.

Industry/Entity Type

University

Requirements
Must have
• Copy/Text: Please see attached doc. file for copy/text to be used on the front and back of the card.

Front: High color gloss

Back: Black and white only design

Featured Colors: Red, White, and Blue
- Should have a patriotic / U.S. government feel

Logos: Must use the attached Outreach Bureau logo and at least one StudyBridgeNet logo (can use more but not required)

```html
<!DOCTYPE html>
<html lang="en">
<head>
<meta charset="utf-8">
<title>Vietnam Recruitment Tour Postcard</title>
<link rel="stylesheet" href="https://fonts.googleapis.com/css2?family=Archivo+Black&family=Roboto+Condensed:wght@400;700&family=Roboto:wght@400;700&display=swap">
<style>
  :root {
    --stage: #e4e4e6;
    --navy: #16235e;
    --navy-deep: #0c1540;
    --red: #b3161d;
    --red-deep: #6e0a0f;
    --silver: #dfe3ea;
    --silver-dark: #9aa2ae;
    --pink: #f28a8a;
    --white: #ffffff;
    --ink: #111111;
    --paper: #ffffff;
  }
  * { margin: 0; padding: 0; box-sizing: border-box; }
  html, body { width: 1200px; height: 1000px; overflow: hidden; }
  body { background: var(--stage); position: relative; font-family: "Roboto", Arial, sans-serif; }

  .postcard { position: absolute; width: 615px; height: 477px; overflow: hidden;
    box-shadow: 0 2px 8px rgba(0,0,0,.25); }
  .postcard--front { left: 460px; top: 18px; background: var(--navy); }
  .postcard--back { left: 459px; top: 507px; height: 475px; background: var(--paper); }

  .front-art { position: absolute; inset: 0; }
  .flag-area { position: absolute; left: 0; top: 0; width: 340px; height: 205px; }

  .agency-mark { position: absolute; left: 432px; top: 72px; width: 170px;
    display: flex; align-items: center; gap: 10px; }
  .agency-mark__dot { width: 44px; height: 44px; border-radius: 50%; background: var(--silver); flex: none; }
  .agency-mark__name { font-family: "Roboto Condensed", Arial, sans-serif; font-weight: 700;
    font-size: 17px; line-height: 1.15; color: var(--silver); }

  .headline { position: absolute; left: 0; width: 615px; text-align: center; top: 202px;
    font-family: "Archivo Black", Arial, sans-serif; color: var(--silver); font-size: 30px;
    text-shadow: 0 2px 2px rgba(0,0,0,.6); letter-spacing: .5px; }
  .headline__place { font-size: 38px; }
  .subhead { position: absolute; left: 0; width: 615px; text-align: center; top: 246px;
    font-family: "Roboto Condensed", Arial, sans-serif; color: var(--white); font-size: 20px; }

  .tour-dates { position: absolute; left: 0; width: 615px; text-align: center; top: 322px;
    font-family: "Archivo Black", Arial, sans-serif; color: var(--silver); font-size: 20px;
    text-shadow: 0 2px 2px rgba(0,0,0,.6); }
  .tour-dates__day { font-size: 40px; vertical-align: -3px; }
  .registration { position: absolute; left: 0; width: 615px; text-align: center; top: 376px;
    font-family: "Roboto Condensed", Arial, sans-serif; color: var(--pink); font-size: 16px; word-spacing: 1px; }
  .registration__sep { margin: 0 8px; }
  .signup { position: absolute; left: 0; width: 615px; text-align: center; top: 437px;
    font-family: "Roboto Condensed", Arial, sans-serif; color: var(--pink); font-size: 15px; }
  .signup__url { font-weight: 700; }

  .program-mark { position: absolute; right: 14px; top: 412px; display: flex; align-items: center; gap: 6px; }
  .program-mark__dot { width: 9px; height: 9px; border-radius: 50%; background: var(--white); }
  .program-mark__name { font-family: "Roboto Condensed", Arial, sans-serif; font-size: 16px; color: var(--white); }

  .save-band { position: absolute; left: 0; top: 0; width: 463px; height: 153px;
    background: linear-gradient(180deg, #050505 0%, #1c1c1c 55%, #3a3a3a 78%, #0a0a0a 100%); color: var(--white);
    font-family: "Roboto Condensed", Arial, sans-serif; }
  .save-band__title { position: absolute; left: 18px; top: 19px; font-family: "Archivo Black", Arial, sans-serif;
    font-size: 19px; color: var(--silver); text-shadow: 0 1px 1px #000; }
  .save-band__intro { position: absolute; left: 192px; top: 21px; width: 270px; font-size: 9.5px; line-height: 13px; }
  .save-band__note { position: absolute; left: 77px; top: 55px; font-size: 9.5px; }
  .schedule { position: absolute; top: 81px; font-size: 9.5px; line-height: 14px; border-collapse: collapse; }
  .schedule td { padding: 0; vertical-align: top; }
  .schedule td:first-child { width: 58px; }
  .schedule--left { left: 77px; }
  .schedule--right { left: 296px; }
  .save-band__contact { position: absolute; left: 16px; top: 132px; font-size: 14px; }
  .save-band__email { font-family: "Roboto", Arial, sans-serif; font-weight: 700; }

  .address-divider { position: absolute; left: 298px; top: 170px; width: 1px; height: 270px;
    background: linear-gradient(180deg, transparent, #c8c8c8 40%, #c8c8c8 60%, transparent); }
</style>
</head>
<body>

<section class="postcard postcard--front" aria-label="Postcard front">
  <svg class="front-art" width="615" height="477" viewBox="0 0 615 477" aria-hidden="true">
    <defs>
      <linearGradient id="navyField" x1="0" y1="0" x2="1" y2="1">
        <stop offset="0" stop-color="#22357e"/>
        <stop offset="1" stop-color="#0c1540"/>
      </linearGradient>
      <linearGradient id="redField" x1="0" y1="0" x2="0" y2="1">
        <stop offset="0" stop-color="#c0181f"/>
        <stop offset="1" stop-color="#6e0a0f"/>
      </linearGradient>
      <linearGradient id="silverLine" x1="0" y1="0" x2="1" y2="0">
        <stop offset="0" stop-color="#8a9099"/>
        <stop offset=".35" stop-color="#ffffff"/>
        <stop offset="1" stop-color="#b7bcc4"/>
      </linearGradient>
      <linearGradient id="goldGlow" x1="0" y1="0" x2="1" y2="0">
        <stop offset="0" stop-color="#ffe9a8" stop-opacity=".9"/>
        <stop offset="1" stop-color="#ffe9a8" stop-opacity="0"/>
      </linearGradient>
    </defs>
    <rect width="615" height="477" fill="url(#navyField)"/>
    <path d="M0 300 C60 240 140 205 300 200 L615 195 L615 290 L0 300 Z" fill="#101b4f"/>
    <path d="M0 400 C70 320 180 285 615 270 L615 477 L0 477 Z" fill="url(#redField)"/>
    <path d="M0 400 C70 320 180 285 615 270 L615 276 C190 290 80 325 0 410 Z" fill="url(#silverLine)"/>
    <rect x="0" y="244" width="330" height="2" fill="url(#goldGlow)"/>
    <circle cx="14" cy="245" r="7" fill="#fff6d8"/>
  </svg>
  <div class="flag-area" role="img" aria-label="Waving American flag illustration"
       style="background: linear-gradient(160deg, #1d2f7a 0%, #2a3f8f 38%, #c8323a 52%, #f2f2f2 60%, #b3161d 70%, rgba(22,35,94,0) 100%);"></div>

  <div class="agency-mark">
    <span class="agency-mark__dot"></span>
    <span class="agency-mark__name">Federal Bureau<br>of Outreach</span>
  </div>

  <h1 class="headline">Join us in <span class="headline__place">VIETNAM</span></h1>
  <p class="subhead">for the Off The Beaten Track (OTBT) Tour</p>
  <p class="tour-dates">September <span class="tour-dates__day">29</span> – October <span class="tour-dates__day">03</span></p>
  <p class="registration">Registration is FREE<span class="registration__sep">|</span>Space is limited</p>
  <p class="signup">Sign up today at <span class="signup__url">go.outreach-example.org/OTBT_Vietnam</span></p>

  <div class="program-mark">
    <span class="program-mark__dot"></span>
    <span class="program-mark__name">StudyBridgeNet</span>
  </div>
</section>

<section class="postcard postcard--back" aria-label="Postcard back">
  <div class="save-band">
    <h2 class="save-band__title">Save the dates!</h2>
    <p class="save-band__intro">Spend one week visiting northern Vietnam’s best gifted and talented high schools that are “off the beaten track” of most U.S. recruiters.</p>
    <p class="save-band__note">Tour will originate from and return to Hanoi Transportation provided by Outreach Bureau Hanoi Office</p>
    <table class="schedule schedule--left">
      <tr><td>Sept 29 (Mo)</td><td>: Hung Yen &amp; Nam Dinh Provinces</td></tr>
      <tr><td>Sept 30 (Tu)</td><td>: Ninh Binh Province</td></tr>
      <tr><td>Oct 1 (We)</td><td>: Thanh Hoa Province</td></tr>
    </table>
    <table class="schedule schedule--right">
      <tr><td>Oct 2 (Th)</td><td>: Nghe An Province</td></tr>
      <tr><td>Oct 3 (Fr)</td><td>: Thai Binh Province</td></tr>
    </table>
    <p class="save-band__contact">For Inquiries Email: <span class="save-band__email">hanoi.studybridgenet@outreach-example.org</span></p>
  </div>
  <div class="address-divider"></div>
</section>

</body>
</html>
```